Im want a website LIKE VRX's and FleetHollow.com's with product payment options like Trenzo's

I need a website LIKE VRX with a header made EXACTLY LIKE THAT OF FLEETHOLLOWS .

The front page photo should be like that of FLEETHOLLOW's webpage as well.

The name of the website will be called "M.K. (Caldera Key)".

We will be targeting ALL MARKETS in a small town in central Panama and charging businesses "listing fees" like a phone book does but also providing informational blogs, news, and other interesting activities.

THIS IS A MULTI PAGE WEBSITE

THIS IS WHERE VRX's website meets Brivelle/FleetHollow.

Once the layout is built I will tweak and modify, add information, and upload items for sale.

Here is a list of specific categories that should be listed out above the front page header image/search bar

-- Home -- News -- Travel -- Activities -- Shop & Dine -- Store -- More... --

These categories should be spread across the bottom of the page in three sections:

WHATS SO GREAT ABOUT (Caldera Key),
HAND PICKED TOURS
ACTIVITIES etc.

Also lets use www.Trenzo.example 's
"HOT DESTINATIONS"
"BEAT THE BEST PRICES IN BOQUETE"
"OCTOBERS INSIDER PICKS"
"TOP DESTINATIONS"
and spread them in four sections side-by-side near the bottom of the page.

Overall I would like to see the finished product to be something LIKE VRX's and FleetHollows.

WE NEED ONLINE PAYMENT OPTIONS LIKE BRIVELLE'S WEBSITE HAS

This will be a desktop website but should be very mobile friendly as well.

-rodmund

P.S. Good luck!

If it isn't already too late to change the website name, the name of the website should be "Caldera Key". Added Friday, October 9, 2015

What do you guys think the budget should be to win this? Added Saturday, October 10, 2015

www.palmorra.example is the most amazing simple site. Whoever can make me a replica with my specifications will win immediately!!!! Added Sunday, October 18, 2015

OMG www.palmorra.example is the bomb!So simple and elegant. Whoever can make me an EXACT REPLICA OF WWW.PALMORRA.EXAMPLE as my site with the specifications mentioned in my brief will take home the $825.00 immediately! Good luck amigos! Added Sunday, October 18, 2015

Does anybody know how to add recurring monthly billing options on this website? Added Sunday, October 18, 2015

ALL MARKETS

Product

Coded - Design and coding required

5+ page

• Coinvey payment options.
• I must be able to add and remove photos/text and video from the HTML files in the page.
• Be creative my friends, and may the odds be forever in your favor!
• I added some photos of a good layout for our page below.

```html
<!DOCTYPE html>
<html lang="en">
<head>
<meta charset="utf-8">
<title>Caldera Key — Targeting tourism</title>
<link rel="stylesheet" href="https://fonts.googleapis.com/css2?family=Open+Sans:wght@400;600;700&display=swap">
<style>
  :root{
    --teal:#2a9fb3;
    --teal-dark:#1f8597;
    --ink:#3a3a3a;
    --muted:#8a8a8a;
    --line:#e2e2e2;
    --paper:#ffffff;
    --page:#f6f6f6;
    --accent:#e0a21c;
    --footer:#1e1e1e;
    --star:#f2b01e;
    --hero-top:#4f9fcf;
    --hero-bottom:#3aa9b6;
    --photo-a:#5fb3cf;
    --photo-b:#4ab0b0;
    --photo-c:#c9b08f;
  }
  *{box-sizing:border-box;margin:0;padding:0}
  html,body{width:828px;height:1200px;overflow:hidden}
  body{font-family:"Open Sans",Arial,sans-serif;color:var(--ink);background:var(--paper);position:relative}

  .hero{position:absolute;left:0;top:0;width:828px;height:412px;
    background:linear-gradient(180deg,var(--hero-top) 0%,var(--hero-bottom) 100%)}

  .topnav{position:absolute;left:50px;top:26px;width:728px;height:38px;background:var(--teal);
    display:flex;align-items:center;padding:0 14px 0 10px;border-radius:2px;box-shadow:0 2px 4px rgba(0,0,0,.2)}
  .topnav a{color:#fff;text-decoration:none;font-size:10px;font-weight:600;margin-right:32px;line-height:38px}
  .topnav a.current{background:var(--teal-dark);padding:0 12px}
  .topnav .login{margin-left:auto;margin-right:0;background:#fff;color:var(--teal);padding:0 14px;line-height:22px;border-radius:2px;font-size:9px;display:flex;align-items:center;gap:5px}

  .brand{position:absolute;top:166px;width:828px;text-align:center;color:#fff}
  .brand h1{font-size:34px;font-weight:700;letter-spacing:.5px;line-height:1.15}
  .brand p{font-size:10px;margin-top:2px;letter-spacing:.5px}
  .search{position:absolute;left:300px;top:250px;width:228px;height:24px;background:#fff;border-radius:2px;
    font-size:9px;color:var(--muted);display:flex;align-items:center;padding:0 10px;justify-content:space-between}

  .welcome{position:absolute;top:424px;width:828px;text-align:center}
  .welcome h2{font-size:18px;font-weight:600;line-height:1.3}
  .welcome .sub{font-size:8px;color:var(--muted);margin-top:2px}
  .features{position:absolute;top:474px;left:60px;width:708px;display:flex;justify-content:space-between}
  .feature{width:210px;text-align:center}
  .feature svg{height:26px;display:block;margin:0 auto 6px}
  .feature h3{font-size:9px;font-weight:700;color:var(--teal);letter-spacing:.3px}
  .feature p{font-size:8px;line-height:1.55;color:var(--muted);margin-top:6px}

  .divider{position:absolute;top:628px;left:60px;width:708px;border-top:1px solid var(--line)}

  .services{position:absolute;top:650px;left:0;width:828px;height:468px;background:var(--page)}
  .services h2{text-align:center;font-size:20px;font-weight:600;margin-top:68px;line-height:1.3}
  .services .intro{width:560px;margin:12px auto 0;text-align:center;font-size:8px;line-height:1.6;color:var(--muted)}
  .cards{position:absolute;top:170px;left:60px;width:708px;display:flex;justify-content:space-between}
  .card{width:226px;background:#fff;border:1px solid var(--line);padding:8px 8px 12px}
  .card .photo{height:150px;position:relative}
  .card .price{position:absolute;right:0;bottom:10px;background:rgba(0,0,0,.65);color:#fff;font-size:7px;padding:3px 8px;line-height:1.3;text-align:right}
  .card .price b{display:block;font-size:11px}
  .card h3{font-size:10px;font-weight:700;color:var(--teal);margin-top:10px}
  .rating{display:flex;align-items:center;gap:6px;font-size:8px;color:var(--teal);margin-top:4px}
  .stars{color:var(--star);letter-spacing:1px;font-size:9px}
  .card p{font-size:8px;line-height:1.55;color:var(--muted);margin-top:6px}
  .photo.swim{background:var(--photo-a)}
  .photo.boat{background:var(--photo-b)}
  .photo.family{background:var(--photo-c)}

  .footer{position:absolute;top:1124px;left:0;width:828px;height:76px;background:var(--footer);color:#fff;
    display:flex;align-items:center;padding:0 60px;justify-content:space-between}
  .footer .logo b{display:block;font-size:16px;font-weight:700}
  .footer .logo span{font-size:8px;color:#bbb}
  .footer .promo{display:flex;align-items:center;gap:10px;font-size:7px;line-height:1.4;color:#ddd;width:230px}
  .footer .promo i{width:30px;height:30px;border-radius:50%;background:var(--accent);flex:none}
  .footer .copy{font-size:7px;color:#aaa}
</style>
</head>
<body>

<div class="hero" role="img" aria-label="Photo of a tropical beach with cliffs, turquoise sea and a wooden boat"></div>

<nav class="topnav">
  <a class="current" href="#">Home ▾</a>
  <a href="#">About Us ▾</a>
  <a href="#">Accommodation</a>
  <a href="#">Rooms</a>
  <a href="#">Gallery</a>
  <a href="#">Blog</a>
  <a href="#">Contact</a>
  <a class="login" href="#">
    <svg width="9" height="9" viewBox="0 0 10 10"><path d="M1 5h6M5 2l3 3-3 3" stroke="currentColor" stroke-width="1.5" fill="none"/></svg>
    LOGIN
  </a>
</nav>

<header class="brand">
  <h1>Caldera Key</h1>
  <p>Targeting tourism</p>
</header>

<div class="search">
  <span>Search by places</span>
  <svg width="10" height="10" viewBox="0 0 10 10"><circle cx="4" cy="4" r="3" stroke="#888" stroke-width="1.2" fill="none"/><path d="M6.3 6.3L9 9" stroke="#888" stroke-width="1.2"/></svg>
</div>

<section class="welcome">
  <h2>Welcome To Caldera Key</h2>
  <p class="sub">Targeting tourism in a small town in central Panama</p>
</section>

<div class="features">
  <div class="feature">
    <svg viewBox="0 0 30 26" width="30"><rect x="3" y="3" width="24" height="17" rx="3" fill="#d9534f"/><rect x="6" y="6" width="8" height="6" fill="#fff"/><rect x="16" y="6" width="8" height="6" fill="#fff"/><circle cx="9" cy="22" r="2.5" fill="#444"/><circle cx="21" cy="22" r="2.5" fill="#444"/></svg>
    <h3>GUIDED TOURS</h3>
    <p>Explore hidden beaches, jungle trails and coffee farms with friendly local guides who know every corner of the island.</p>
  </div>
  <div class="feature">
    <svg viewBox="0 0 30 26" width="30"><rect x="7" y="2" width="16" height="22" fill="#3a78c2"/><g fill="#fff"><rect x="10" y="5" width="3" height="3"/><rect x="17" y="5" width="3" height="3"/><rect x="10" y="11" width="3" height="3"/><rect x="17" y="11" width="3" height="3"/></g><rect x="13" y="18" width="4" height="6" fill="#fff"/></svg>
    <h3>HOTELS/HOSTELS</h3>
    <p>Compare cosy hostels and seaside hotels, read honest reviews and book your stay with secure online payment options.</p>
  </div>
  <div class="feature">
    <svg viewBox="0 0 34 26" width="34"><path d="M3 17l3-7h20l4 7v4H3z" fill="#4a6fd0"/><rect x="9" y="11" width="7" height="5" fill="#cfe0ff"/><rect x="18" y="11" width="6" height="5" fill="#cfe0ff"/><circle cx="9" cy="21" r="3" fill="#333"/><circle cx="25" cy="21" r="3" fill="#333"/></svg>
    <h3>RENTAL VEHICLES</h3>
    <p>Rent scooters, jeeps and boats by the day or week, with pickup right at the dock and no hidden fees.</p>
  </div>
</div>

<div class="divider"></div>

<section class="services">
  <h2>Our Services</h2>
  <p class="intro">From sunrise boat trips to evening food tours, our local partners offer something for every traveller. Browse trusted listings, compare prices and book your next island adventure in minutes with secure checkout and instant confirmation from the host.</p>

  <div class="cards">
    <article class="card">
      <div class="photo swim" role="img" aria-label="Photo of friends swimming in the sea">
        <div class="price">from USD<b>$79.99</b></div>
      </div>
      <h3>GUIDED TOURS</h3>
      <div class="rating"><span class="stars">★★★★★</span>156 Reviews</div>
      <p>Spend a full day on the water, snorkel the coral garden and enjoy fresh fruit on a quiet sandy cove.</p>
    </article>
    <article class="card">
      <div class="photo boat" role="img" aria-label="Photo of a longtail boat on a lagoon">
        <div class="price">from USD<b>$79.99</b></div>
      </div>
      <h3>GUIDED TOURS</h3>
      <div class="rating"><span class="stars">★★★★★</span>156 Reviews</div>
      <p>Hop aboard a longtail boat and visit three small islands, with lunch and snorkel gear included in the price.</p>
    </article>
    <article class="card">
      <div class="photo family" role="img" aria-label="Photo of a family on a sunny beach">
        <div class="price">from USD<b>$79.99</b></div>
      </div>
      <h3>GUIDED TOURS</h3>
      <div class="rating"><span class="stars">★★★★★</span>156 Reviews</div>
      <p>A relaxed family trip along the coast with shallow swimming spots, games on the beach and a picnic.</p>
    </article>
  </div>
</section>

<footer class="footer">
  <div class="logo"><b>Caldera Key</b><span>Targeting tourism</span></div>
  <div class="promo"><i></i><span>Get a special price code when you book your first trip with us today</span></div>
  <div class="copy">© 2015 All Rights Reserved - Caldera Key</div>
</footer>

</body>
</html>
```